Web Design Services Create a Similar website to my Competitor

We would like a similar website designed like our main competitor with all the features there website has and more. Also we would like to accept payments through our website and to rank quickly with seo based on our home page and other page use of high traffic keywords. this is the website we would like to have ours designed similar to https://www.harbourpetalstudio.com. we will be providing the same services and more just at a different location. We would also like to know be able to easily make adjustments to the website when its time to edit it please thanks.

Basically I am looking to have have similar website built almost exactly the same but with my logo, and other personalized information to my company Rosalind Marigold Beauty Lounge. I will need to send you model images and logo design idea but the body and user interface of my competitor https://www.harbourpetalstudio.com will be exactly the same. I can be reached anytime to answer any questions you may have.
Updates

Hi Designers I would like to clarify some information Harbour Petal Studio is my Competitor we are not affiliated. I would like my website to be designed similar to hers but please do not take any content from her website to put on mine I will be providing images to be posted on my website. Also please do not use any of her videos or YouTube videos on my website to avoid any legal issues. Thanks for your understanding.

Target Market(s)

Make up Application Services For Events and Lindenbrook Summer Festival

Industry/Entity Type

Beauty and Makeup Application and services

Coding

Coded - Design and coding required

Number of Pages Required

5+ page

Font styles to use
Sans Serif

Colors
E54698
E96AAD
F1A4CE
F9D9EA
FCEFF6
A7469A
B969AE
D3A5CF
EDDBEB
F8F0F9

Requirements
Must have
• Must be similar to my competitor, need a video section, testimonial and must be easily able to navigate to information sections and book now payment notifications running on all pages so customers can easily book there spot for 2026 carnival
Nice to have
• I am looking to have a similar website to https://www.harbourpetalstudio.com created but make it as minimal and modern
Should not have
• Project can be coded if it makes it easier to create a similar look to my competitor just ask that updates can easily be made later on.

```html
<!DOCTYPE html>
<html lang="en">
<head>
<meta charset="utf-8">
<title>Rosalind Marigold Beauty Lounge</title>
<link href="https://fonts.googleapis.com/css2?family=Young+Serif&family=Poppins:wght@400;500;600&display=swap" rel="stylesheet">
<style>
:root{
  --pink:#e54698;
  --pink-soft:#e96aad;
  --plum:#a7469a;
  --ink:#000;
  --panel:#161516;
  --row:#1c1b1c;
  --line:#3a2a33;
  --text:#fff;
  --muted:#d9d9d9;
}
*{margin:0;padding:0;box-sizing:border-box}
html,body{width:1200px;height:5333px;overflow:hidden;background:var(--ink);color:var(--text);font-family:"Poppins",sans-serif}
.page{position:relative;width:1200px;height:5333px}
.abs{position:absolute}
.serif{font-family:"Young Serif",serif;font-weight:400}
.pink{color:var(--pink)}
.ph{position:absolute}
.btn{position:absolute;display:flex;align-items:center;justify-content:center;border-radius:30px;font-size:12px;font-weight:500;text-transform:uppercase;letter-spacing:.3px;color:#fff;white-space:nowrap}
.btn-fill{background:var(--pink)}
.btn-line{border:2px solid var(--pink);background:#0d0d0d}
.center{left:0;width:1200px;text-align:center}

/* nav */
.nav a{position:absolute;top:66px;font-size:12px;font-weight:500;color:#fff;text-decoration:none;text-transform:uppercase}
.nav a.active{color:var(--pink)}
.brand{position:absolute;left:475px;top:50px;width:250px;text-align:center}
.brand b{display:block;font-family:"Young Serif",serif;font-weight:400;font-size:22px;color:var(--pink);line-height:1;white-space:nowrap}
.brand span{display:block;font-size:10px;letter-spacing:2.5px;color:var(--pink);margin-top:6px;line-height:14px}

/* hero */
.hero{left:0;top:0;width:1200px;height:620px;background:linear-gradient(90deg,#050505 35%,#2a1210 60%,#5a2418 78%,#1a0a08 100%)}
.hero-title{left:110px;top:168px;font-size:36px;line-height:66px;color:var(--pink)}
.hero-text{left:110px;top:313px;width:560px;font-size:14px;line-height:36px}

/* stats */
.stat{position:absolute;top:1258px;width:220px;text-align:center}
.stat h3{font-family:"Young Serif",serif;font-weight:400;font-size:26px}
.stat p{margin-top:22px;font-size:13px;line-height:34px;color:var(--pink);text-transform:uppercase}

/* services */
.services{left:103px;top:1440px;width:1097px;height:805px;background:var(--panel);border-top-left-radius:70px}
.svc{position:absolute;left:63px;width:956px;height:114px;background:var(--row);border:1px solid #2b2a2b;border-radius:14px}
.svc .icon{position:absolute;left:26px;top:32px;width:50px;height:50px;border-radius:8px;background:#242324}
.svc .name{position:absolute;left:142px;top:0;height:114px;display:flex;align-items:center;width:220px;font-size:15px;font-weight:500;line-height:36px;color:var(--pink);text-transform:uppercase}
.svc ul{position:absolute;left:424px;top:26px;list-style:none;font-size:13px;line-height:38px}
.svc li::before{content:"";display:inline-block;width:5px;height:5px;border-radius:50%;background:var(--pink);margin-right:14px;vertical-align:middle}
.svc .btn{left:786px;top:37px;width:148px;height:40px}

/* faq */
.faq{position:absolute;left:161px;width:878px;height:50px;background:#1b1a1b;border-bottom:1px solid var(--line);display:flex;align-items:center;justify-content:space-between;padding:0 30px;font-size:12px;font-weight:500;text-transform:uppercase}
.faq i{width:0;height:0;border-left:5px solid transparent;border-right:5px solid transparent;border-top:6px solid #fff}

/* footer */
.footer{left:0;top:4958px;width:1200px;height:375px;background:#161516}
.flink{position:absolute;font-size:14px}
.dot{position:absolute;top:5190px;width:26px;height:26px;border:2px solid #fff;border-radius:50%}
</style>
</head>
<body>
<div class="page">

  <section class="abs hero">
    <div class="ph" role="img" aria-label="Portrait of a carnival performer in festive painted makeup with red roses" style="left:640px;top:0;width:560px;height:620px;background:radial-gradient(ellipse at 55% 40%,#8a3a24 0%,#4a1a12 45%,transparent 75%)"></div>
  </section>

  <nav class="nav">
    <a class="active" style="left:110px">Home</a>
    <a style="left:193px">Services</a>
    <a style="left:302px">Gallery</a>
    <a style="left:409px">Pricing</a>
    <a style="left:737px">Testimonials</a>
    <a style="left:881px">FAQs</a>
  </nav>
  <div class="brand"><b>Rosalind Marigold</b><span>CARNIVAL<br>BEAUTY LOUNGE</span></div>
  <div class="btn btn-line" style="left:966px;top:56px;width:122px;height:40px;font-size:11px">Book Now</div>

  <h1 class="abs serif hero-title">Glow Beyond the Road:<br>Your Carnival Beauty Starts Here</h1>
  <p class="abs hero-text">Now Booking for Carnival 2026 – Secure Your Spot Today Your All-In-One Carnival Beauty Concierge Because You Deserve a Stress-Free Start to the Road.</p>
  <div class="btn btn-fill" style="left:110px;top:450px;width:232px;height:40px">Choose Your Destination</div>

  <h2 class="abs serif center pink" style="top:664px;font-size:30px;line-height:58px">Create Happy Memories At The Biggest &amp;<br>The Best Carnival Of Year!</h2>

  <div class="ph" role="img" aria-label="Video still of a costumed carnival group posing together" style="left:215px;top:818px;width:770px;height:387px;border-radius:26px;background:linear-gradient(135deg,#2a1c10,#6a4a1c 40%,#3a1a22 75%,#1a1010)"></div>
  <svg class="abs" style="left:572px;top:985px" width="56" height="56" viewBox="0 0 56 56"><circle cx="28" cy="28" r="28" fill="#e54698"/><path d="M22 17 L40 28 L22 39Z" fill="#fff"/></svg>

  <div class="stat" style="left:164px"><h3>2,000+</h3><p>Faces Beat To<br>Perfection</p></div>
  <div class="stat" style="left:384px"><h3>10+ Cities</h3><p>Traveled For<br>On-Location Glam</p></div>
  <div class="stat" style="left:590px"><h3>7+ Years</h3><p>Glam<br>Experience</p></div>
  <div class="stat" style="left:797px"><h3>5-Star Rated</h3><p>500+<br>Happy Clients</p></div>

  <section class="abs services">
    <h2 class="abs serif pink" style="left:64px;top:68px;font-size:30px">Flawless. Fast. Festival-Ready</h2>
    <div class="svc" style="top:164px"><div class="icon"></div><div class="name">Carnival Makeup<br>Application</div><ul><li>Soft Glam (natural radiance)</li><li>Full Glam (bold eyes, glitter, lashes)</li></ul><div class="btn btn-line">Register Now</div></div>
    <div class="svc" style="top:315px"><div class="icon"></div><div class="name">Hair Styling</div><ul><li>Wig installs &amp; styling</li><li>Festival-proof finishing sprays</li></ul><div class="btn btn-fill">See Packages</div></div>
    <div class="svc" style="top:464px"><div class="icon"></div><div class="name">Group Glam<br>Packages</div><ul><li>Group discounts</li><li>Bottle of bubbly (on premium bookings)</li></ul><div class="btn btn-line">Register Now</div></div>
    <div class="svc" style="top:615px"><div class="icon"></div><div class="name">Travel &amp;<br>On-Location Glam</div><ul><li>Vacation rental setups</li><li>Day-of-location touch-ups</li></ul><div class="btn btn-line">Register Now</div></div>
  </section>

  <h2 class="abs serif center pink" style="top:2320px;font-size:30px">What You'll Need</h2>
  <p class="abs" style="left:185px;top:2393px;width:830px;text-align:center;font-size:14px;line-height:36px">Prepare for glam like a pro. At Rosalind Marigold Beauty Lounge, we believe Carnival is more than an event — it's a celebration of beauty, culture, and confidence. Our glam squad specializes in high-impact beauty looks that are bold, lasting, and tailored to your unique vibe.</p>
  <div class="ph" role="img" aria-label="Close-up of glitter eye makeup" style="left:112px;top:2569px;width:231px;height:330px;border-radius:14px;background:linear-gradient(135deg,#2a3a9a,#7a3aa0 50%,#c07070)"></div>
  <div class="ph" role="img" aria-label="Model wearing an ornate gold masquerade mask" style="left:360px;top:2600px;width:232px;height:335px;border-radius:14px;background:linear-gradient(160deg,#2a2420,#8a6a40 50%,#3a2a1a)"></div>
  <div class="ph" role="img" aria-label="Profile of a model with red lips and jewelled shoulder" style="left:610px;top:2569px;width:230px;height:330px;border-radius:14px;background:linear-gradient(135deg,#1a1614,#6a5a50 50%,#2a2220)"></div>
  <div class="ph" role="img" aria-label="Model wearing a red lace masquerade mask" style="left:857px;top:2600px;width:229px;height:335px;border-radius:14px;background:linear-gradient(160deg,#0a0a0a,#8a1a24 50%,#3a1a14)"></div>
  <div class="btn btn-line" style="left:497px;top:2994px;width:206px;height:40px">Book Now For 2026</div>

  <section class="abs" style="left:0;top:3119px;width:1200px;height:449px;background:#0e0d0e">
    <div class="ph" role="img" aria-label="Stacked gold masquerade masks" style="left:0;top:0;width:125px;height:449px;background:linear-gradient(90deg,#5a4a30,#1a1510)"></div>
    <div class="ph" role="img" aria-label="Stacked gold masquerade masks" style="right:0;top:0;width:160px;height:449px;background:linear-gradient(270deg,#5a4a30,#1a1510)"></div>
  </section>
  <h2 class="abs serif center pink" style="top:3185px;font-size:30px">What Our Clients Are Saying</h2>
  <div class="abs center" style="top:3268px;font-size:22px;letter-spacing:6px;color:#f5c518">★★★★★</div>
  <p class="abs serif center" style="top:3324px;font-size:19px">"I've never felt so confident on the road."</p>
  <p class="abs center" style="top:3382px;font-size:14px;line-height:38px">The Rosalind Marigold team made me feel like a queen. My makeup didn't budge all day — even after 10 hours<br>of nonstop dancing!</p>
  <p class="abs center pink" style="top:3484px;font-size:13px">– DARIA M., 2024 CARNIVAL CLIENT</p>
  <svg class="abs" style="left:137px;top:3326px" width="32" height="32" viewBox="0 0 32 32"><circle cx="16" cy="16" r="15" fill="none" stroke="#fff" stroke-width="1.5"/><path d="M18 10 L12 16 L18 22" fill="none" stroke="#fff" stroke-width="2"/></svg>
  <svg class="abs" style="left:1027px;top:3326px" width="32" height="32" viewBox="0 0 32 32"><circle cx="16" cy="16" r="15" fill="none" stroke="#fff" stroke-width="1.5"/><path d="M14 10 L20 16 L14 22" fill="none" stroke="#fff" stroke-width="2"/></svg>

  <h2 class="abs serif center pink" style="top:3648px;font-size:30px">Frequently Asked Questions</h2>
  <div class="faq" style="top:3740px">Do I need to bring my own makeup or hair products?<i></i></div>
  <div class="faq" style="top:3821px">How early should I book for Carnival 2026?<i></i></div>
  <div class="faq" style="top:3902px">What happens if I'm late?<i></i></div>
  <div class="faq" style="top:3984px">What should I do to prep before my appointment?<i></i></div>
  <div class="faq" style="top:4065px">Do you offer mobile/on-location glam?<i></i></div>

  <div class="ph" role="img" aria-label="Video still of a model in a black and gold filigree masquerade mask" style="left:0;top:4198px;width:1200px;height:428px;background:radial-gradient(ellipse at 50% 45%,#6a5030 0%,#2a2018 35%,#0a0a0c 70%)"></div>
  <svg class="abs" style="left:572px;top:4384px" width="56" height="56" viewBox="0 0 56 56"><circle cx="28" cy="28" r="28" fill="#e54698"/><path d="M22 17 L40 28 L22 39Z" fill="#fff"/></svg>

  <div class="ph" role="img" aria-label="Pink lace masquerade mask decoration" style="left:0;top:4800px;width:440px;height:158px;background:linear-gradient(90deg,rgba(229,70,152,.35),rgba(229,70,152,0))"></div>
  <h2 class="abs serif pink" style="left:110px;top:4690px;width:420px;font-size:28px;line-height:58px">Still thinking? The girls who booked already know – the road hits different</h2>
  <p class="abs" style="left:610px;top:4692px;width:500px;font-size:14px;line-height:36px">The girls who booked already know — when your glam is locked in, the road feels effortless. Don't miss out on your Carnival glow-up. Secure your spot now.</p>
  <div class="btn btn-line" style="left:610px;top:4830px;width:248px;height:42px">Choose Your Destination</div>

  <footer class="abs footer">
    <div class="abs" style="left:420px;top:0;width:1px;height:300px;background:#2e2d2e"></div>
    <div class="abs" style="left:820px;top:0;width:1px;height:300px;background:#2e2d2e"></div>
  </footer>
  <h4 class="abs serif pink" style="left:110px;top:5018px;font-size:22px">Stay in the Glow</h4>
  <div class="abs" style="left:110px;top:5088px;width:250px;height:38px;border-radius:20px;background:#222122;font-size:12px;padding:11px 18px">Your Email Address</div>
  <div class="btn btn-line" style="left:110px;top:5146px;width:148px;height:36px;font-size:11px">Subscribe Now</div>
  <h4 class="abs serif pink" style="left:495px;top:5018px;font-size:22px">Quick Links</h4>
  <span class="flink" style="left:495px;top:5080px">Home</span>
  <span class="flink" style="left:495px;top:5122px">Services</span>
  <span class="flink" style="left:495px;top:5164px">Gallery</span>
  <span class="flink" style="left:495px;top:5206px">Pricing</span>
  <span class="flink" style="left:626px;top:5080px">FAQs</span>
  <span class="flink" style="left:626px;top:5122px">Book Now</span>
  <span class="flink" style="left:626px;top:5164px">Terms &amp; Conditions</span>
  <span class="flink" style="left:626px;top:5206px">Privacy Policy</span>
  <div class="abs" style="left:840px;top:5050px;width:290px;text-align:center">
    <div class="serif pink" style="font-size:28px;line-height:1.1;white-space:nowrap">Rosalind Marigold</div>
    <div class="pink" style="font-size:13px;letter-spacing:3px;margin-top:8px;line-height:18px">CARNIVAL<br>BEAUTY LOUNGE</div>
  </div>
  <div class="dot" style="left:912px"></div>
  <div class="dot" style="left:942px"></div>
  <div class="dot" style="left:972px"></div>
  <div class="dot" style="left:1002px"></div>
  <div class="dot" style="left:1032px"></div>
  <p class="abs center" style="top:5294px;font-size:11px">© 2025 ROSALIND MARIGOLD BEAUTY LOUNGE. ALL RIGHTS RESERVED.</p>

</div>
</body>
</html>
```